Business Card Design for a Software Startup

We'd like to have a business card design. We already have a logo. Basically what we need is a clean design with name, address, cellphone and phone numbers, e-mail and web site address (front) and a space on the back with our logo with the company name on the right side and some texts on the bottom.
We are a development and consulting company in Brazil with highly qualified team of professionals in Java, iOS and Android development and consulting.

Target Market(s)

CIO, IT managers of mid to big size companies

Industry/Entity Type

Business

```html
<!DOCTYPE html>
<html lang="en">
<head>
<meta charset="UTF-8">
<title>Veltra Business Card</title>
<link rel="stylesheet" href="https://fonts.googleapis.com/css2?family=Source+Sans+3:wght@400;600;700&display=swap">
<style>
  :root {
    --canvas: #e9e7e3;
    --card: #ffffff;
    --navy: #0f2f63;
    --blue: #1f6fc0;
    --sky: #2f9be0;
    --ink: #3a3a3a;
    --rule: #c9ccd2;
    --shadow: rgba(0, 0, 0, 0.18);
  }
  * { margin: 0; padding: 0; box-sizing: border-box; }
  html, body {
    width: 1200px;
    height: 720px;
    overflow: hidden;
    background: var(--canvas);
    font-family: "Source Sans 3", "Helvetica Neue", Arial, sans-serif;
  }
  .canvas {
    position: relative;
    width: 1200px;
    height: 720px;
    display: flex;
    align-items: center;
    justify-content: center;
    gap: 40px;
  }
  .card {
    position: relative;
    width: 540px;
    height: 310px;
    background: var(--card);
    box-shadow: 0 6px 18px var(--shadow);
    overflow: hidden;
  }

  /* Front: contact side */
  .card-front .swoosh {
    position: absolute;
    inset: 0;
    width: 100%;
    height: 100%;
  }
  .brand-block {
    position: absolute;
    left: 40px;
    top: 34px;
    display: flex;
    flex-direction: column;
    align-items: flex-start;
  }
  .brand-square {
    width: 78px;
    height: 78px;
    border-radius: 10px;
    background: var(--blue);
    margin-left: 22px;
    margin-bottom: 10px;
  }
  .brand-name {
    font-weight: 700;
    font-size: 40px;
    letter-spacing: 1px;
    color: var(--navy);
    line-height: 1;
  }
  .divider {
    position: absolute;
    left: 262px;
    top: 26px;
    width: 1px;
    height: 130px;
    background: var(--rule);
  }
  .contact-list {
    position: absolute;
    left: 278px;
    top: 26px;
    list-style: none;
    font-size: 14px;
    color: var(--ink);
    line-height: 19px;
  }
  .contact-list li {
    display: flex;
    align-items: center;
    gap: 6px;
  }
  .contact-list svg {
    width: 11px;
    height: 11px;
    flex: none;
  }
  .address {
    position: absolute;
    left: 278px;
    top: 114px;
    font-size: 14px;
    line-height: 18px;
    color: var(--ink);
    font-style: normal;
  }
  .holder {
    position: absolute;
    left: 86px;
    top: 246px;
    color: #ffffff;
    text-align: center;
  }
  .holder-name {
    font-weight: 700;
    font-size: 19px;
    line-height: 1.1;
  }
  .holder-title {
    font-weight: 400;
    font-size: 14px;
  }

  /* Back: brand side */
  .card-back .brand-wordmark {
    position: absolute;
    left: 0;
    right: 0;
    top: 90px;
    text-align: center;
    font-weight: 700;
    font-size: 96px;
    letter-spacing: 2px;
    color: var(--navy);
    line-height: 1;
  }
  .card-back .web {
    position: absolute;
    right: 70px;
    bottom: 48px;
    font-size: 17px;
    letter-spacing: 4px;
    color: var(--ink);
  }
</style>
</head>
<body>
<main class="canvas">

  <section class="card card-front" aria-label="Business card front">
    <svg class="swoosh" viewBox="0 0 540 310" preserveAspectRatio="none" aria-hidden="true">
      <defs>
        <linearGradient id="band" x1="0" y1="0" x2="1" y2="0">
          <stop offset="0" stop-color="#3aa6e8"/>
          <stop offset="0.6" stop-color="#1f6fc0"/>
          <stop offset="1" stop-color="#0f2f63"/>
        </linearGradient>
      </defs>
      <path d="M0 222 C150 258 340 214 540 160 L540 182 C390 220 230 276 150 310 L0 310 Z" fill="url(#band)"/>
      <path d="M0 212 C160 246 350 202 540 150" fill="none" stroke="#0f2f63" stroke-width="3"/>
      <path d="M0 204 C170 236 360 194 540 142" fill="none" stroke="#1f6fc0" stroke-width="1"/>
    </svg>

    <div class="brand-block">
      <div class="brand-square"></div>
      <div class="brand-name">VELTRA</div>
    </div>

    <div class="divider"></div>

    <ul class="contact-list">
      <li>
        <svg viewBox="0 0 12 12"><circle cx="6" cy="6" r="6" fill="#0f2f63"/><path d="M4 3 L5 5 L4.5 5.6 Q5.5 7 6.4 7.5 L7 7 L9 8 L8.4 9 Q5 9 3 4 Z" fill="#fff"/></svg>
        123-456-7890
      </li>
      <li>
        <svg viewBox="0 0 12 12"><rect x="3.5" y="1" width="5" height="10" rx="1" fill="#0f2f63"/><rect x="4.3" y="2.2" width="3.4" height="6" fill="#fff"/></svg>
        456-085-4321
      </li>
      <li>
        <svg viewBox="0 0 12 12"><circle cx="6" cy="6" r="6" fill="#0f2f63"/><rect x="3" y="4" width="6" height="4" fill="#fff"/><path d="M3 4 L6 6.3 L9 4" fill="none" stroke="#0f2f63" stroke-width="0.7"/></svg>
        yourname@veltra.com
      </li>
      <li>
        <svg viewBox="0 0 12 12"><circle cx="6" cy="6" r="5.4" fill="none" stroke="#0f2f63" stroke-width="1.2"/><ellipse cx="6" cy="6" rx="2.2" ry="5.4" fill="none" stroke="#0f2f63" stroke-width="0.9"/><line x1="0.6" y1="6" x2="11.4" y2="6" stroke="#0f2f63" stroke-width="0.9"/></svg>
        www.veltra.com
      </li>
    </ul>

    <address class="address">
      Door No. Street Name<br>
      City Name, State, Zip Code
    </address>

    <div class="holder">
      <div class="holder-name">Your Name</div>
      <div class="holder-title">Title</div>
    </div>
  </section>

  <section class="card card-back" aria-label="Business card back">
    <div class="brand-wordmark">VELTRA</div>
    <div class="web">www.veltra.com</div>
  </section>

</main>
</body>
</html>
```